Modern Medical Optometry Website

We need mordern, Patient friendly website. Easy to navigate and enhance our advance medical technology and excellent patient care.
1. HOME PAGE
2. OUR TEAM PAGE
3. EYECARE PAGE - VISION SERVICES, EYE EXAMS, KERATOCONUS CENTER, GLAUCOMA , DIABITES, MELORIDEX EXAM, DIGITAL RETINAL, OCT.
4. MYOPIA CONTROL CLINIC
5. DRY EYE CLINIC
6. EYEWEAR
7. PATIENT CENTER - BLOG
7. CONTACT US
This is our current website www.brivaloka.com
and We want to add more content and a cleaner design like these website
http://tarnwickfolvendale.com/
https://www.qmvorlu.com/

```html
<!DOCTYPE html>
<html lang="en">
<head>
<meta charset="utf-8">
<title>Lumora Optometry</title>
<link href="https://fonts.googleapis.com/css2?family=Lato:wght@400;700;900&display=swap" rel="stylesheet">
<style>
:root{
  --yellow:#f2c21b;
  --yellow-soft:#f8d350;
  --ink:#1e1e1e;
  --grey:#666;
  --footer:#333333;
  --footer-bar:#2a2a2a;
  --white:#fff;
}
*{margin:0;padding:0;box-sizing:border-box}
html,body{width:1200px;height:3377px;overflow:hidden}
body{font-family:'Lato',sans-serif;color:var(--ink);background:var(--white);position:relative}
.abs{position:absolute}
/* header */
.site-header{left:0;top:0;width:1200px;height:115px;background:var(--white)}
.brand{left:160px;top:38px;font-weight:900;font-size:22px;color:var(--yellow);display:flex;align-items:center;gap:10px}
.brand-mark{width:20px;height:20px;background:var(--yellow)}
.top-links{left:620px;top:22px;display:flex;gap:40px;font-size:16px;align-items:center}
.phone{font-weight:700;display:flex;gap:8px;align-items:center}
.main-nav{left:374px;top:68px;display:flex;gap:18px;font-size:15px;color:#555}
.main-nav .active{font-weight:900;color:var(--ink)}
/* hero */
.hero{left:0;top:115px;width:1200px;height:551px;background:radial-gradient(ellipse at 55% 40%,#6b5a4c 0%,#3d3129 45%,#1f1915 100%)}
.hero-text{left:0;top:190px;width:1200px;text-align:center;color:var(--white)}
.hero-text .pre{font-size:34px;font-weight:700}
.hero-text h1{font-size:54px;font-weight:700;letter-spacing:1px;margin-top:2px}
.btn-outline{display:inline-block;border:3px solid var(--white);color:var(--white);font-size:17px;font-weight:700;padding:10px 26px;margin-top:14px}
.hero-arrow{width:52px;height:52px;border-radius:50%;background:rgba(200,200,200,.75)}
/* eyecare */
.section-title{width:1200px;left:0;text-align:center;font-size:32px;font-weight:400;letter-spacing:1px}
.title-rule{left:575px;width:50px;height:4px;background:var(--ink)}
.service{width:231px;height:230px;color:var(--white);font-weight:900;font-size:20px;text-align:center;display:flex;flex-direction:column;justify-content:flex-end;padding-bottom:36px;line-height:1.1}
.service.yellow{background:var(--yellow);justify-content:center;padding:0}
.service.photo{background:linear-gradient(160deg,#6a6a6a,#2c2c2c)}
.service .btn-outline{font-size:13px;padding:6px 18px;border-width:2px;margin:14px auto 0}
.chev{font-size:46px;color:#888;font-weight:400}
/* myopia */
.myopia{left:0;top:1146px;width:1200px;height:491px;background:var(--yellow-soft)}
.myopia-photo{left:0;top:1146px;width:1200px;height:491px}
.myopia-copy{left:110px;top:1245px;width:480px;text-align:center}
.myopia-copy h2{font-size:31px;font-weight:900}
.myopia-copy .rule{width:40px;height:4px;background:var(--ink);margin:12px auto 18px}
.myopia-copy p{font-size:16px;line-height:1.75}
.btn-dark{display:inline-block;border:3px solid var(--ink);font-size:16px;font-weight:700;padding:10px 36px;margin-top:22px}
/* patient center */
.post{width:282px;height:347px;background:var(--white);box-shadow:0 3px 12px rgba(0,0,0,.12)}
.post-img{width:282px;height:164px;background:linear-gradient(135deg,#e6e0cc,#b7ad95)}
.post-date{left:0;top:150px;background:var(--yellow);color:var(--white);font-size:13px;padding:6px 20px 6px 36px}
.post-body{padding:26px 26px 0}
.post-body h3{font-size:16px;font-weight:700;line-height:1.35}
.post-body p{font-size:12.5px;color:#888;line-height:1.45;margin-top:12px}
.post-body .more{font-size:13px;font-weight:900;color:var(--yellow);margin-top:20px;display:block}
/* testimonials */
.testimonials{left:0;top:2184px;width:1200px;height:374px;background:linear-gradient(120deg,#4a3e35,#2b241f 60%,#3a2f27)}
.testimonials h2{left:0;top:2060px;width:1200px}
.t-title{left:0;top:2243px;width:1200px;text-align:center;color:var(--yellow);font-size:30px}
.t-rule{left:580px;top:2285px;width:40px;height:4px;background:var(--yellow)}
.t-portrait{left:313px;top:2348px;width:108px;height:106px;background:linear-gradient(160deg,#d9b98a,#8a6a4a)}
.t-quote{left:470px;top:2340px;font-size:60px;color:var(--white);font-weight:900;line-height:1}
.t-copy{left:529px;top:2348px;width:450px;color:var(--white);font-size:15px;line-height:1.4}
.t-author{left:529px;top:2437px;color:var(--white);font-size:13px;font-weight:700}
.dot{width:11px;height:11px;border-radius:50%;border:2px solid var(--white);top:2494px}
.dot.on{background:var(--white)}
/* map */
.map{left:0;top:2558px;width:1200px;height:421px;background:linear-gradient(135deg,#d8d8d8,#bdbdbd 55%,#cfcfcf)}
/* footer */
.footer{left:0;top:2979px;width:1200px;height:331px;background:var(--footer);color:#ddd}
.f-head{font-size:17px;font-weight:900;color:var(--white)}
.f-col{font-size:15px;line-height:1.65}
.f-col .name{font-size:19px;line-height:1.4}
.f-links{font-size:13px;font-weight:700;line-height:2.15;color:var(--white)}
.social{display:flex;align-items:center;gap:12px;font-size:14px;height:34px}
.social i{width:24px;height:24px;border-radius:50%;background:#e89b2a;display:block}
.footer-bar{left:0;top:3310px;width:1200px;height:67px;background:var(--footer-bar);color:#999;font-size:13px;text-align:center;line-height:67px}
</style>
</head>
<body>
<header class="site-header abs">
  <div class="brand abs"><span class="brand-mark"></span>Lumora Optometry</div>
  <div class="top-links abs">
    <span class="phone"><svg width="18" height="18" viewBox="0 0 24 24"><path fill="#f2c21b" d="M6.6 10.8a15 15 0 0 0 6.6 6.6l2.2-2.2c.3-.3.7-.4 1-.2 1.1.4 2.3.6 3.6.6.6 0 1 .4 1 1V20c0 .6-.4 1-1 1A17 17 0 0 1 3 4c0-.6.4-1 1-1h3.5c.6 0 1 .4 1 1 0 1.3.2 2.5.6 3.6.1.3 0 .7-.2 1z"/></svg>555-014-2010</span>
    <span>PATIENT CENTER</span><span>CONTACT US</span>
  </div>
  <nav class="main-nav abs"><span class="active">HOME</span><span>OUR TEAM</span><span>EYECARE</span><span>MYOPIA CONTROL CLINIC</span><span>DRY EYE CLINIC</span><span>EYEWEAR</span></nav>
</header>

<section class="hero abs" role="img" aria-label="Close-up photograph of a human eye"></section>
<div class="hero-text abs">
  <div class="pre">WELCOME TO</div>
  <h1>LUMORA OPTOMETRY</h1>
  <span class="btn-outline">LEARN MORE</span>
</div>
<div class="hero-arrow abs" style="left:129px;top:334px"><svg width="52" height="52"><path d="M30 17l-9 9 9 9" stroke="#222" stroke-width="3" fill="none"/></svg></div>
<div class="hero-arrow abs" style="left:1014px;top:334px"><svg width="52" height="52"><path d="M22 17l9 9-9 9" stroke="#222" stroke-width="3" fill="none"/></svg></div>

<h2 class="section-title abs" style="top:700px">EYECARE</h2>
<div class="title-rule abs" style="top:748px"></div>
<span class="chev abs" style="left:88px;top:862px">‹</span>
<div class="service yellow abs" style="left:130px;top:777px">VISION<br>SERVICES<span class="btn-outline">LEARN MORE</span></div>
<div class="service photo abs" style="left:371px;top:817px" role="img" aria-label="Optometrist performing an eye exam">EYE EXAMS</div>
<div class="service photo abs" style="left:610px;top:777px" role="img" aria-label="Keratoconus care photograph">KERATOCONUS<br>CENTER</div>
<div class="service photo abs" style="left:851px;top:817px;background:linear-gradient(160deg,#7a5a44,#2a1c14)" role="img" aria-label="Close-up of an eye for digital retinal imaging">DIGITAL RETINAL</div>
<span class="chev abs" style="left:1094px;top:882px">›</span>

<section class="myopia abs"></section>
<svg class="myopia-photo abs" width="1200" height="491" role="img" aria-label="Optometrist examining a patient with a slit lamp"><defs><linearGradient id="mp" x1="0" y1="0" x2="1" y2="1"><stop offset="0" stop-color="#e8e6e2"/><stop offset="1" stop-color="#9a9590"/></linearGradient></defs><polygon points="675,0 1200,0 1200,491 513,491" fill="url(#mp)"/></svg>
<div class="myopia-copy abs">
  <h2>MYOPIA CONTROL CLINIC</h2>
  <div class="rule"></div>
  <p>Pellentesque faucibus Ut accumsan ultricies elit Maecenas at justo id velit placerat molestie Donec dictum lectus non Cras a ante vitae enim iaculis<br>aliquam Mauris nunc quam venenatis nec euismod sit amet egestas placerat est Pellentesque habitant m</p>
  <span class="btn-dark">LEARN MORE</span>
</div>

<h2 class="section-title abs" style="top:1688px">PATIENT CENTER</h2>
<div class="title-rule abs" style="top:1738px"></div>
<article class="post abs" style="left:153px;top:1774px"><div class="post-img" role="img" aria-label="Exam room with equipment"></div><span class="post-date abs">JAN 20, 2019</span><div class="post-body"><h3>Lorem ipsum dolor sit amet con-sectetuer adipiscing elit Nam</h3><p>Duis quam Nam eget lacus Aliquam erat volutpat Quisque dignissim congue leo Mauris vel lacus vitae felis</p><span class="more">READ MORE ›</span></div></article>
<article class="post abs" style="left:459px;top:1774px"><div class="post-img" role="img" aria-label="Clinic team group photo" style="background:linear-gradient(135deg,#d8c24a,#5a5046)"></div><span class="post-date abs">JAN 20, 2019</span><div class="post-body"><h3>Lorem ipsum dolor sit amet con-sectetuer adipiscing elit Nam</h3><p>Duis quam Nam eget lacus Aliquam erat volutpat Quisque dignissim congue leo Mauris vel lacus vitae felis</p><span class="more">READ MORE ›</span></div></article>
<article class="post abs" style="left:765px;top:1774px"><div class="post-img" role="img" aria-label="Child having an eye test" style="background:linear-gradient(135deg,#e0b23a,#6a5040)"></div><span class="post-date abs">JAN 20, 2019</span><div class="post-body"><h3>Lorem ipsum dolor sit amet con-sectetuer adipiscing elit Nam</h3><p>Duis quam Nam eget lacus Aliquam erat volutpat Quisque dignissim congue leo Mauris vel lacus vitae felis</p><span class="more">READ MORE ›</span></div></article>

<section class="testimonials abs" role="img" aria-label="Dimmed photograph of eye exam equipment"></section>
<div class="t-title abs">TESTIMONIALS</div>
<div class="t-rule abs"></div>
<div class="t-portrait abs" role="img" aria-label="Portrait of the reviewer"></div>
<div class="t-quote abs">“</div>
<p class="t-copy abs">Pellentesque faucibus Ut accumsan ultricies elit Maecenas at justo id velit placerat molestie Donec dictum lectus non odio Cras a ante vitae enim iaculis aliquam Mauris nunc quam venenatis nec euismod sit amet egestas placerat est</p>
<div class="t-author abs">BY AUTHOR NAME</div>
<span class="dot abs" style="left:575px"></span><span class="dot on abs" style="left:594px"></span><span class="dot abs" style="left:613px"></span>

<section class="map abs" role="img" aria-label="Map showing the two clinic locations"></section>
<svg class="abs" style="left:506px;top:2750px" width="32" height="44" viewBox="0 0 24 34"><path d="M12 0C5 0 0 5 0 12c0 9 12 22 12 22s12-13 12-22C24 5 19 0 12 0z" fill="#111"/><circle cx="12" cy="12" r="4.5" fill="#fff"/></svg>
<svg class="abs" style="left:731px;top:2795px" width="32" height="44" viewBox="0 0 24 34"><path d="M12 0C5 0 0 5 0 12c0 9 12 22 12 22s12-13 12-22C24 5 19 0 12 0z" fill="#111"/><circle cx="12" cy="12" r="4.5" fill="#fff"/></svg>

<footer class="footer abs">
  <div class="f-head abs" style="left:162px;top:77px">CONTACT US</div>
  <div class="f-col abs" style="left:162px;top:112px"><div class="name">Lumora Optometry</div>4410 Halvern Ave.,<br>Pinecourt, CA 90001<br>Phone. 555-014-2010<br>Fax. 555-014-2070<br>Email. info@brivaloka.com</div>
  <div class="f-col abs" style="left:414px;top:118px"><div class="name">Alder Crest</div>2208 Quillmore St.,<br>Suite 4,<br>Alder Crest, CA 90002<br>Phone. 555-019-4020<br>Email. aldercrest@brivaloka.com</div>
  <div class="f-head abs" style="left:732px;top:77px">QUICK LINKS</div>
  <div class="f-links abs" style="left:734px;top:112px">OUR TEAM<br>EYECARE<br>MYOPIA CONTROL CLINIC<br>DRY EYE CLINIC<br>EYEWEAR</div>
  <div class="f-head abs" style="left:921px;top:77px">GET IN TOUCH</div>
  <div class="abs" style="left:921px;top:110px">
    <div class="social"><i></i>Chirpline</div>
    <div class="social"><i></i>Faceplace</div>
    <div class="social"><i></i>Workgrid</div>
    <div class="social"><i></i>Snapfolio</div>
  </div>
</footer>
<div class="footer-bar abs">Copyright © 2019 All right reserved</div>
</body>
</html>
```